Business Cards Design for the electrical wholesaler: clean bold dynamic :)

We need a business card design that would follow our latest brand guidelines. As an electrical wholesaler we want to bring a fresh look and feel into the industry. The design should be clean bold and dynamic. It should come alive with the renewed energy of our green colour. Our grey colour should keep things balanced and complement the notion of maturity and responsibility. We employ Lato as a corporate font however are not bound by this font and we’re open to interpretation here.

Target Market(s)

Electrical contractors

Industry/Entity Type

Business

Contact Information for Business Card

Logo
Name & Surname: Halyna Dorosh
Job Title: Director of Marketing
Email: halya.dorosh@quillmail.example
Cell phone: XXX.XXX.XXXX
Address: 20517 - 87 Ave. Edmonton, AB, Canada. T6K 4N8
Business Phone: 780.555.0184
Website: www.brovix.example

Font styles to use
Other font styles liked:
• Lato

Requirements
Must have
• Logo & website
Nice to have
• Brand elements - some of them you may find in the attached Brand Guidelines (e.g. three lines on the background signifying "W")

```html
<!DOCTYPE html>
<html lang="en">
<head>
<meta charset="utf-8">
<title>Brovix Business Cards</title>
<link rel="stylesheet" href="https://fonts.googleapis.com/css2?family=Oswald:wght@600&family=Work+Sans:wght@400;500;600&display=swap">
<style>
  :root {
    --brand-green: #8dc63f;
    --brand-green-light: #9ccd4c;
    --ink-grey: #4a4a4a;
    --soft-grey: #5c5c5c;
    --paper: #ffffff;
    --backdrop: #ecebe8;
  }
  * { box-sizing: border-box; margin: 0; padding: 0; }
  html, body { width: 1200px; height: 930px; overflow: hidden; }
  body {
    background: var(--backdrop);
    font-family: "Work Sans", sans-serif;
    position: relative;
  }
  .card {
    position: absolute;
    width: 560px;
    height: 320px;
    box-shadow: 0 6px 18px rgba(0,0,0,0.18);
  }
  .card-front {
    left: 60px; top: 90px;
    background: linear-gradient(135deg, var(--brand-green) 0%, var(--brand-green-light) 100%);
  }
  .brand-lockup {
    position: absolute;
    left: 0; right: 0; top: 118px;
    display: flex; align-items: center; justify-content: center; gap: 14px;
  }
  .brand-dot {
    width: 22px; height: 22px; border-radius: 50%;
    background: var(--paper);
  }
  .brand-name {
    font-weight: 600;
    font-size: 64px;
    line-height: 1;
    color: var(--paper);
    letter-spacing: -1px;
  }
  .front-web {
    position: absolute;
    right: 150px; bottom: 40px;
    font-size: 14px; font-weight: 500;
    color: var(--paper);
    letter-spacing: 0.5px;
  }
  .card-back {
    left: 580px; top: 520px;
    background: var(--paper);
  }
  .identity {
    position: absolute;
    right: 302px; top: 104px;
    text-align: right;
    white-space: nowrap;
  }
  .person-name {
    font-family: "Oswald", sans-serif;
    font-weight: 600;
    font-size: 34px;
    line-height: 1;
    color: var(--brand-green);
    letter-spacing: 0.3px;
  }
  .person-role {
    margin-top: 5px;
    font-size: 14px;
    color: var(--ink-grey);
    letter-spacing: 0.4px;
  }
  .divider {
    position: absolute;
    left: 270px; top: 94px;
    width: 2px; height: 88px;
    background: var(--brand-green);
  }
  .contact-list {
    position: absolute;
    left: 286px; top: 96px;
    list-style: none;
  }
  .contact-list li {
    display: flex; align-items: center; gap: 9px;
    font-size: 14px; line-height: 21px;
    color: var(--ink-grey);
    white-space: nowrap;
  }
  .contact-list svg { width: 11px; height: 11px; flex: none; }
  .accent { color: var(--brand-green); }
  .address {
    position: absolute;
    left: 0; right: 0; bottom: 48px;
    text-align: center;
    font-size: 14px;
    color: var(--soft-grey);
    letter-spacing: 0.6px;
  }
</style>
</head>
<body>

<section class="card card-front" aria-label="Card front">
  <div class="brand-lockup">
    <span class="brand-dot"></span>
    <span class="brand-name">brovix</span>
  </div>
  <p class="front-web">www.brovix.example</p>
</section>

<section class="card card-back" aria-label="Card back">
  <div class="identity">
    <h1 class="person-name">HALYNA DOROSH</h1>
    <p class="person-role">Director of Marketing</p>
  </div>
  <span class="divider"></span>
  <ul class="contact-list">
    <li>
      <svg viewBox="0 0 12 12" aria-hidden="true"><path d="M2.5 1 L4.5 1 L5.2 3.5 L4 4.5 Q5 7 7.5 8 L8.5 6.8 L11 7.5 L11 9.5 Q10.5 11 9 11 Q1 10 1 2.5 Q1 1 2.5 1 Z" fill="#8dc63f"/></svg>
      <span>780.555.0184</span>
    </li>
    <li>
      <svg viewBox="0 0 12 12" aria-hidden="true"><rect x="3" y="0.8" width="6" height="10.4" rx="1.2" fill="none" stroke="#8dc63f" stroke-width="1.3"/><circle cx="6" cy="9.2" r="0.8" fill="#8dc63f"/></svg>
      <span>780.555.0147</span>
    </li>
    <li>
      <svg viewBox="0 0 12 12" aria-hidden="true"><rect x="1" y="2.5" width="10" height="7" fill="none" stroke="#8dc63f" stroke-width="1.4"/><path d="M1 2.5 L6 6.5 L11 2.5" fill="none" stroke="#8dc63f" stroke-width="1.4"/></svg>
      <span>halya.dorosh@quillmail.example</span>
    </li>
    <li>
      <svg viewBox="0 0 12 12" aria-hidden="true"><circle cx="6" cy="6" r="5" fill="none" stroke="#8dc63f" stroke-width="1.3"/><ellipse cx="6" cy="6" rx="2" ry="5" fill="none" stroke="#8dc63f" stroke-width="1"/><line x1="1" y1="6" x2="11" y2="6" stroke="#8dc63f" stroke-width="1"/></svg>
      <span>www.<span class="accent">brovix</span>.example</span>
    </li>
  </ul>
  <p class="address">20517 - 87 Ave. Edmonton, AB, Canada. T6K 4N8</p>
</section>

</body>
</html>
```